Colin Vardek Business card

Hey there, I’m hoping to have a business card designed. I’m in Real estate and just switched to a new Brokerage called: The Harbourline Property Group

The back could just be the company name maybe or whatever looks good!

I’ve attached some logos of our company and some cards my buddy had done up.

On the card:
Colin Vardek
colinvardek@mailora.com
587-412-9065
colinvardek.ca

Target Market(s)

Home buyers and sellers

Industry/Entity Type

Real Estate

Contact Information for Business Card

just looking for a cool and modern design with my picture on it. I like the idea of Black and red being used.

Requirements
Must have
• all the details provided. I'm open to anything. Just want a professional looking card.

```html
<!DOCTYPE html>
<html lang="en">
<head>
<meta charset="UTF-8">
<title>Colin Vardek Business Card</title>
<link href="https://fonts.googleapis.com/css2?family=Montserrat:wght@400;500;700;800&display=swap" rel="stylesheet">
<style>
  :root {
    --bg: #e9e8e9;
    --paper: #ffffff;
    --ink: #111111;
    --black: #070a0c;
    --red: #d0223a;
    --white: #ffffff;
  }
  * { margin: 0; padding: 0; box-sizing: border-box; }
  html, body {
    width: 1200px;
    height: 1108px;
    overflow: hidden;
    background: var(--bg);
    font-family: "Montserrat", Arial, sans-serif;
  }
  .canvas { position: relative; width: 1200px; height: 1108px; }

  .card { position: absolute; width: 750px; height: 458px; }
  .card-front { left: 240px; top: 62px; background: var(--paper); }
  .card-back { left: 240px; top: 589px; height: 441px; background: var(--black); }

  .front-info { position: absolute; left: 0; top: 0; width: 376px; height: 100%; }
  .brand-name {
    position: absolute;
    left: 33px;
    top: 40px;
    width: 240px;
    font-weight: 800;
    font-size: 24px;
    line-height: 1.12;
    color: var(--ink);
    text-transform: uppercase;
  }
  .agent-name {
    position: absolute;
    left: 33px;
    top: 243px;
    font-weight: 700;
    font-size: 27px;
    color: var(--red);
  }
  .agent-title {
    position: absolute;
    left: 33px;
    top: 280px;
    font-size: 16px;
    font-weight: 500;
    color: var(--ink);
  }
  .contact-list {
    position: absolute;
    left: 32px;
    top: 328px;
    list-style: none;
  }
  .contact-item {
    display: flex;
    align-items: center;
    height: 33px;
    font-size: 16px;
    font-weight: 500;
    color: var(--ink);
  }
  .contact-icon { width: 17px; height: 17px; margin-right: 11px; flex: none; }

  .accent-stripe {
    position: absolute;
    left: 376px;
    top: 0;
    width: 7px;
    height: 100%;
    background: var(--red);
  }
  .portrait-panel {
    position: absolute;
    left: 383px;
    top: 0;
    width: 367px;
    height: 100%;
    background: var(--black);
  }
  .portrait {
    position: absolute;
    left: 55px;
    top: 45px;
    width: 275px;
    height: 413px;
    border-radius: 120px 120px 0 0;
    background: linear-gradient(180deg, #3a3230 0%, #2b3038 45%, #23272e 100%);
  }

  .back-brand {
    position: absolute;
    left: 0;
    right: 0;
    top: 168px;
    text-align: center;
    font-weight: 800;
    font-size: 46px;
    line-height: 1.12;
    color: var(--white);
    text-transform: uppercase;
  }
</style>
</head>
<body>
<main class="canvas">

  <section class="card card-front" aria-label="Business card front">
    <div class="front-info">
      <p class="brand-name">The Harbourline Property Group</p>
      <h1 class="agent-name">Colin Vardek</h1>
      <p class="agent-title">Owner</p>
      <ul class="contact-list">
        <li class="contact-item">
          <svg class="contact-icon" viewBox="0 0 24 24" aria-hidden="true">
            <path fill="#d0223a" d="M6.6 10.8a15.1 15.1 0 0 0 6.6 6.6l2.2-2.2a1 1 0 0 1 1-.25 11.4 11.4 0 0 0 3.6.57 1 1 0 0 1 1 1V20a1 1 0 0 1-1 1A17 17 0 0 1 3 4a1 1 0 0 1 1-1h3.5a1 1 0 0 1 1 1c0 1.25.2 2.45.57 3.57a1 1 0 0 1-.25 1z"/>
          </svg>
          587-412-9065
        </li>
        <li class="contact-item">
          <svg class="contact-icon" viewBox="0 0 24 24" aria-hidden="true">
            <rect x="2" y="5" width="20" height="14" rx="1.5" fill="#d0223a"/>
            <path d="M3 6.5l9 6.5 9-6.5" fill="none" stroke="#fff" stroke-width="1.6"/>
          </svg>
          colinvardek@mailora.com
        </li>
        <li class="contact-item">
          <svg class="contact-icon" viewBox="0 0 24 24" aria-hidden="true">
            <circle cx="12" cy="12" r="10" fill="#d0223a"/>
            <path d="M2 12h20M12 2c3 3 3 17 0 20M12 2c-3 3-3 17 0 20" fill="none" stroke="#fff" stroke-width="1.4"/>
          </svg>
          www.colinvardek.ca
        </li>
      </ul>
    </div>
    <div class="accent-stripe"></div>
    <div class="portrait-panel">
      <div class="portrait" role="img" aria-label="Portrait photo of Colin Vardek in a dark suit and white shirt"></div>
    </div>
  </section>

  <section class="card card-back" aria-label="Business card back">
    <p class="back-brand">The Harbourline<br>Property Group</p>
  </section>

</main>
</body>
</html>
```